New Business Card for Web Design/Internet Marketing Company

Looking for a great looking new business card. We are a 10 year old web design, internet marketing and website management company that works mostly with small businesses.

Our new card needs to better match the colors and style of our website, be bold, extremely usable and slightly edgy.

Target Market(s)

Small/Medium businesses that have websites

Industry/Entity Type

Internet

Requirements
Must have
• Front and back design, full color, rounded corners please

Must use the colors/style of our website (JPG provided)

INFO FOR CARDS (as readable as possible please)
Mark Lenner
President/CEO
mark@trelvanmedia.example
Phone: 520-381-7459
Toll Free: 866-381-7459
Address: 4315 W. Calloway Ave. Ste. 140, Tucson, AZ 85792

THINGS I WANT TO PROMOTE (if there is room):
1. Our Website - www.trelvanmedia.example

2. Social Media
Twitter: @trelvanmedia
Facebook: www.facebook.com/trelvanmedia

3. Our Services
Web Design
Internet Marketing
Website Management

```html
<!DOCTYPE html>
<html lang="en">
<head>
<meta charset="utf-8">
<title>Trelvan Media – Business Card</title>
<link rel="stylesheet" href="https://fonts.googleapis.com/css2?family=Source+Sans+3:wght@400;600;700&display=swap">
<style>
  :root {
    --backdrop: #ece6dc;
    --card-navy: #0c1729;
    --brand-orange: #f0832a;
    --brand-blue: #2a9fd8;
    --text-light: #f2f4f7;
    --divider: #6d7684;
  }
  * { margin: 0; padding: 0; box-sizing: border-box; }
  html, body {
    width: 1200px; height: 1040px; overflow: hidden;
    background: var(--backdrop);
    font-family: "Source Sans 3", "Myriad Pro", Arial, sans-serif;
  }
  .canvas { position: relative; width: 1200px; height: 1040px; }
  .card {
    position: absolute; width: 738px; height: 422px;
    background: var(--card-navy);
    box-shadow: 0 2px 6px rgba(0,0,0,.18);
  }
  .card--front { left: 93px; top: 67px; }
  .card--back  { left: 393px; top: 534px; }

  /* Front */
  .person {
    position: absolute; top: 30px; left: 0; width: 100%;
    text-align: center; white-space: nowrap;
  }
  .person__name { color: var(--brand-orange); font-weight: 700; font-size: 27px; }
  .person__title { color: var(--brand-blue); font-size: 21px; margin-left: 4px; }

  .brand-name {
    color: var(--brand-orange); font-weight: 700; white-space: nowrap;
    display: flex; align-items: center;
  }
  .brand-name__dot {
    display: inline-block; border-radius: 50%; background: var(--brand-blue);
  }
  .card--front .brand-name {
    position: absolute; left: 40px; top: 178px; font-size: 40px; gap: 12px;
  }
  .card--front .brand-name__dot { width: 22px; height: 22px; }

  .divider {
    position: absolute; left: 398px; top: 143px; width: 2px; height: 196px;
    background: var(--divider);
  }
  .contact {
    position: absolute; left: 428px; top: 158px; list-style: none;
    color: var(--text-light); font-size: 18.5px; line-height: 26.5px;
  }
  .contact__item { display: flex; align-items: center; gap: 9px; }
  .contact__icon { width: 13px; height: 13px; flex: none; }
  .address {
    position: absolute; left: 428px; top: 281px;
    color: var(--text-light); font-size: 18.5px; line-height: 26px;
  }

  /* Back */
  .card--back .brand-name {
    position: absolute; left: 0; top: 100px; width: 100%;
    justify-content: center; font-size: 52px; gap: 16px;
  }
  .card--back .brand-name__dot { width: 28px; height: 28px; }

  .services {
    position: absolute; left: 0; top: 255px; width: 100%;
    text-align: center; color: var(--brand-orange);
    font-weight: 700; font-size: 23.5px; line-height: 31px;
  }
  .service { white-space: nowrap; margin: 0 8px; }
  .service::before {
    content: ""; display: inline-block; width: 11px; height: 11px;
    border-radius: 50%; background: var(--brand-blue);
    margin-right: 9px; vertical-align: 3px;
  }
  .social {
    position: absolute; left: 0; top: 355px; width: 100%;
    display: flex; justify-content: center; gap: 22px;
    color: var(--text-light); font-size: 24px;
  }
  .social__handle { display: flex; align-items: center; gap: 8px; }
  .social__mark {
    width: 20px; height: 20px; background: var(--brand-blue); border-radius: 3px;
  }
</style>
</head>
<body>
<main class="canvas">

  <section class="card card--front" aria-label="Card front">
    <p class="person">
      <span class="person__name">Mark Lenner ,</span>
      <span class="person__title">President/CEO</span>
    </p>

    <p class="brand-name"><span class="brand-name__dot"></span>Trelvan Media</p>

    <div class="divider"></div>

    <ul class="contact">
      <li class="contact__item">
        <svg class="contact__icon" viewBox="0 0 16 16" aria-hidden="true">
          <circle cx="8" cy="8" r="7.5" fill="none" stroke="#f0832a" stroke-width="1.5"/>
          <path d="M5 4.5 L6.8 4.5 L7.3 6.6 L6.3 7.4 Q7.3 9.3 8.8 10 L9.6 9 L11.5 9.6 L11.5 11.3 Q6 11.5 5 4.5Z" fill="#f0832a"/>
        </svg>866-381-7459</li>
      <li class="contact__item">
        <svg class="contact__icon" viewBox="0 0 16 16" aria-hidden="true">
          <circle cx="8" cy="8" r="7.5" fill="none" stroke="#f0832a" stroke-width="1.5"/>
          <path d="M5 4.5 L6.8 4.5 L7.3 6.6 L6.3 7.4 Q7.3 9.3 8.8 10 L9.6 9 L11.5 9.6 L11.5 11.3 Q6 11.5 5 4.5Z" fill="#f0832a"/>
        </svg>520-381-7459</li>
      <li class="contact__item">
        <svg class="contact__icon" viewBox="0 0 16 16" aria-hidden="true">
          <rect x="1" y="3.5" width="14" height="10" rx="1.5" fill="#f0832a"/>
          <path d="M1.5 4.5 L8 9 L14.5 4.5" fill="none" stroke="#0c1729" stroke-width="1.4"/>
        </svg>mark@trelvanmedia.example</li>
      <li class="contact__item">
        <svg class="contact__icon" viewBox="0 0 16 16" aria-hidden="true">
          <circle cx="8" cy="8" r="7.5" fill="#f0832a"/>
          <path d="M0.5 8 H15.5 M8 0.5 V15.5 M2 4.5 H14 M2 11.5 H14" stroke="#0c1729" stroke-width="1"/>
        </svg>www.trelvanmedia.example</li>
    </ul>

    <p class="address">4315 W. Calloway Ave. Ste. 140<br>Tucson, AZ 85792</p>
  </section>

  <section class="card card--back" aria-label="Card back">
    <p class="brand-name"><span class="brand-name__dot"></span>Trelvan Media</p>

    <p class="services">
      <span class="service">Web Design</span>
      <span class="service">Internet Marketing</span><br>
      <span class="service">Website Management</span>
    </p>

    <div class="social">
      <span class="social__handle"><span class="social__mark"></span>@trelvanmedia</span>
      <span class="social__handle"><span class="social__mark"></span>trelvanmedia</span>
    </div>
  </section>

</main>
</body>
</html>
```